Letterhead Design for Law Firm

**Edit: I have added the photo of a bottom that I like.

------
We are looking for a re-design of our new letterhead. The letterhead is for a law firm and will be used for digital and traditionally printed correspondence.

Here are some suggestions:

- Please use colours are #8ec900 and simple black.
- Please do not use any type of "waves" at the bottom of the page. This is not in style at all.
- Please stay modern yet conservative.
- Please use font Segoe UI Light or similar if you can
- Avoid clipart or illustrations.
- Utilize ample white space in the layout so the design looks clean and information is easy to read at a glance. Don't overcrowd the letterhead.
- Make sure the letterhead design is consistent with our brand identity (see corvelith.ca)
-Please, no black headers or footers.

I am attaching my current letterhead and signature for your convenience.

Remember, the letterhead is an extension of our professional identity. We are a successful firm and trial lawyers who correspond with insurers, judges, lawyers, courts, clients, etc. Make it new, modern, attractive, yet powerful and conservative.

It needs to be easily printable. I would like the bleed removed in print so the black bar the bottom crosses the page (but the text is not near the edges)
Updates

Low design quality

Target Market(s)

Clients, Government Offices, Judiciary, Lawyers, Insurance Companies, Colleagues.

Industry/Entity Type

Law

Other font styles liked:
• Segoe UI LIght, Calibri Light,

Colors
00AB8E
00BBA5
67D7C9
C6EFE9
E9F9F6

Requirements
Must have
• Everything that is on the letterhead now.
Nice to have
• Cutting Edge design, yet conservative.
Should not have
• law firm cliche design, images,

```html
<!DOCTYPE html>
<html lang="en">
<head>
<meta charset="utf-8">
<title>Marrowby Personal Injury Lawyers – Letterhead</title>
<link href="https://fonts.googleapis.com/css2?family=Roboto:wght@300;400;500&family=Roboto+Condensed:wght@400&display=swap" rel="stylesheet">
<style>
  :root{
    --brand-green:#8ec900;
    --ink:#111111;
    --text:#2a2a2a;
    --muted:#555555;
    --paper:#f6f4f4;
    --band:#1c1c1c;
    --rule:#333333;
  }
  html,body{margin:0;padding:0;}
  body{width:935px;height:1200px;overflow:hidden;background:var(--paper);font-family:"Roboto",sans-serif;color:var(--text);}
  .letterhead{position:relative;width:935px;height:1200px;}
  .abs{position:absolute;}
  .brand-name{left:0;width:935px;top:56px;text-align:center;font-size:58px;font-weight:400;letter-spacing:3px;color:var(--ink);line-height:1;}
  .label{font-weight:500;font-size:15px;color:var(--ink);}
  .meta{right:66px;text-align:right;font-size:15.5px;}
  .meta .clerk-name{color:var(--muted);}
  .meta .email{font-size:14px;margin-top:4px;display:flex;justify-content:flex-end;align-items:center;gap:5px;}
  .meta .date{font-size:14.5px;margin-top:11px;}
  .recipient{left:67px;top:266px;font-size:15.5px;line-height:20px;color:var(--ink);}
  .attention{left:67px;top:394px;font-size:15.5px;color:var(--ink);}
  .salutation{left:67px;top:421px;font-size:15.5px;color:var(--ink);}
  .re-label{left:67px;top:459px;font-size:15px;font-weight:500;color:var(--brand-green);}
  .re-block{left:327px;top:491px;font-size:15.5px;line-height:20px;color:var(--ink);}
  .rule{left:63px;width:806px;top:573px;height:1px;background:var(--rule);}
  .body-copy{left:67px;width:802px;top:608px;font-size:11.3px;line-height:18px;color:var(--muted);text-align:justify;}
  .body-copy p{margin:0 0 18px;}
  .closing{left:67px;top:837px;font-size:14px;line-height:17px;color:var(--ink);}
  .signature{left:67px;top:885px;width:230px;height:58px;background:linear-gradient(90deg,rgba(0,0,0,.08),rgba(0,0,0,.02));}
  .signatory{left:69px;top:959px;font-size:14px;line-height:17.5px;color:var(--ink);}
  .contact{left:69px;top:1077px;font-size:13.5px;line-height:19px;color:var(--ink);}
  .contact div{display:flex;align-items:center;gap:6px;}
  .address{right:66px;top:1077px;text-align:right;font-size:14.5px;line-height:19px;color:var(--ink);}
  .accent-line{left:0;width:935px;top:1143px;height:3px;background:var(--brand-green);}
  .practice-band{left:0;width:935px;top:1147px;height:53px;background:var(--band);display:flex;align-items:center;justify-content:center;gap:9px;font-family:"Roboto Condensed",sans-serif;font-size:16.5px;color:#ffffff;}
  .practice-band .sep{color:var(--brand-green);}
</style>
</head>
<body>
<div class="letterhead">
  <div class="abs brand-name">MARROWBY</div>

  <div class="abs label" style="left:67px;top:181px;">Without Prejudice</div>
  <div class="abs label" style="left:67px;top:229px;">By Email</div>

  <div class="abs meta" style="top:184px;">
    <div><span class="label">File Clerk:</span> <span class="clerk-name">Wren Callowell</span></div>
    <div class="email">
      <svg width="12" height="9" viewBox="0 0 12 9"><rect width="12" height="9" fill="#8ec900"/><path d="M0 0 L6 5 L12 0" stroke="#fff" stroke-width="1" fill="none"/></svg>
      wren@corvelith.ca
    </div>
    <div class="date">March 13, 2024</div>
  </div>

  <div class="abs recipient">
    Halvern Insurance Company<br>
    Claims Litigation Department<br>
    48 Linden Crescent North<br>
    P.O. Box 4100<br>
    Waterloo, ON&nbsp;&nbsp; N2A 7K3
  </div>

  <div class="abs attention">Attention:&nbsp; Mr. Dorian Vale</div>
  <div class="abs salutation">Mr. Vale:</div>

  <div class="abs re-label">Re:</div>
  <div class="abs re-block">
    Okafor v. Brandt et al.<br>
    DOL:&nbsp; September 12, 2019<br>
    Pre-Mediation Settlement Proposal – March 13th, 2024
  </div>

  <div class="abs rule"></div>

  <div class="abs body-copy">
    <p>Lorem ipsum dolor sit amet, consectetur adipiscing elit. Donec orci purus, luctus vitae dignissim eu, iaculis sed purus. Vivamus faucibus, ipsum nec aliquet viverra, leo mauris condimentum ligula, sit amet sagittis enim ligula quis arcu. Nam egestas tortor nisi porttitor mattis. In tortor ante, ultricies in suscipit a, tempus non massa. Vivamus et auctor mi. Fusce vel massa nulla. Phasellus nec eros mauris, et scelerisque orci.</p>
    <p>Donec malesuada orci vitae nulla accumsan porta a id massa. Quisque accumsan iaculis magna sit amet fringilla. Maecenas consequat, magna eget tincidunt semper, odio nibh rutrum mi, id feugiat ante nisi eu risus. Vestibulum nunc orci, rhoncus a placerat in, ultricies in mi. Cras mattis varius eros, vel fringilla nisi suscipit eget. Quisque scelerisque sagittis nulla at porttitor.</p>
    <p>Sed id augue vitae urna euismod commodo aliquet a quam. Pellentesque arcu velit, cursus et malesuada ut, consequat et diam. Nullam erat sem, rhoncus id ullamcorper vitae, rhoncus et arcu. In arcu adipiscing lacus, ac bibendum nulla leo eu purus. Quisque nec diam sed risus.</p>
  </div>

  <div class="abs closing">Yours very truly,<br>MARROWBY PERSONAL INJURY LAWYERS</div>
  <div class="abs signature" role="img" aria-label="Handwritten signature of Ellis J. Marrowby"></div>
  <div class="abs signatory">
    Ellis J. Marrowby<br>
    Marrowby Law Professional Corporation<br>
    /wc<br>
    Encl.
  </div>

  <div class="abs contact">
    <div>
      <svg width="13" height="13" viewBox="0 0 24 24"><path fill="#8ec900" d="M6.6 10.8a15.1 15.1 0 0 0 6.6 6.6l2.2-2.2c.3-.3.7-.4 1-.2 1.1.4 2.3.6 3.6.6.6 0 1 .4 1 1V20c0 .6-.4 1-1 1C10.6 21 3 13.4 3 4c0-.6.4-1 1-1h3.5c.6 0 1 .4 1 1 0 1.3.2 2.5.6 3.6.1.3 0 .7-.2 1z"/></svg>
      905-555-0142
    </div>
    <div>
      <svg width="13" height="13" viewBox="0 0 24 24"><rect x="6" y="2" width="12" height="6" fill="#8ec900"/><rect x="2" y="9" width="20" height="8" rx="1" fill="#8ec900"/><rect x="6" y="15" width="12" height="7" fill="#8ec900"/></svg>
      905-555-0178
    </div>
    <div>
      <svg width="13" height="13" viewBox="0 0 24 24" fill="none" stroke="#8ec900" stroke-width="2"><circle cx="12" cy="12" r="9"/><path d="M3 12h18M12 3c3 3 3 15 0 18M12 3c-3 3-3 15 0 18"/></svg>
      www.corvelith.ca
    </div>
  </div>

  <div class="abs address">27 Harbour Street W., Suite 940<br>Hamilton, ON&nbsp; L8R 2K6</div>

  <div class="abs accent-line"></div>
  <div class="abs practice-band">
    <span>Long-Term Disability</span><span class="sep">|</span>
    <span>Serious Personal Injury</span><span class="sep">|</span>
    <span>Child &amp; Pediatric Injury Wrongful Death</span><span class="sep">|</span>
    <span>Employee Terminations</span>
  </div>
</div>
</body>
</html>
```